my website is tavorinque.com. (brand name is ta belle vitrine) This is just a template that i have choose for. The content and the pictures are not about my business just the template.
I would like to have 4 pages for now. 1 homepage, which will be an overview for all pages, it is right now in this way. It will directly highlight my story. My website will tell an exclusive story about details which makes the difference and will make people happy with very small things. It will be art related but very stylish as well. I also want to have a event agenda on my homepage where people can see where my next event is. Page 2 my blog, where I will write weekly about mindset, lifestyle and details. Inspiration place for people who are looking for unique and exclusive approaches in life. Page 3 shop, where I will sell my stuff which is handmade and unique, it will be limited edition stuff. Mostly I will make the designs from marbling art, which I am a teacher for. (https://www.vidoranta.com/watch?v=KpwuzRaxTmo) check this video out for more. Page 4 is book page. Here people will be able to book private or group classes for marbling art (check the video). I have already a community of more than 500 people on gath rix, which will be my public as well. I wanna implement the gath rix button on this page as well. to be able to track.

This is about my website. I also need a logo for my brand, which will suit my website and my goals.

I can also give you a reference website, which really like as structure and style;
https://www.brightorvalco.com/products/the-morning-ledger?gclid=Xr4TpLmwq2HsVD9KEBsZTrc-WkPhyQ-uvlEjdRs3NKaOYFCBWMpuTzG8xyCVbhdnLWRqoaNf_2e8ZtpRvHbAwq9FLQ_hqgQ

Logo Text

ta belle vitrine

Coding

Coded - Design and coding required

Number of Pages Required

4 page

Requirements
Must have
• I can also give you a reference website, which really like as structure and style;
• https://www.brightorvalco.com/products/the-morning-ledger?gclid=Xr4TpLmwq2HsVD9KEBsZTrc-WkPhyQ-uvlEjdRs3NKaOYFCBWMpuTzG8xyCVbhdnLWRqoaNf_2e8ZtpRvHbAwq9FLQ_hqgQ

```html
<!DOCTYPE html>
<html lang="en">
<head>
<meta charset="utf-8">
<title>ta belle vitrine — Home</title>
<link rel="stylesheet" href="https://fonts.googleapis.com/css2?family=Open+Sans:wght@300;400;600;700&family=Roboto:wght@400;500;700&display=swap">
<style>
:root{
  --ink:#1f1f1f;
  --text:#444;
  --muted:#666;
  --orange:#f28a1e;
  --band:#ececec;
  --card:#efefef;
  --line:#d9d9d9;
  --white:#fff;
  --dark:#222;
}
*{box-sizing:border-box;margin:0;padding:0}
html,body{width:1200px;height:3352px;overflow:hidden;background:var(--white)}
body{font-family:"Roboto",Arial,sans-serif;color:var(--text);position:relative}
.abs{position:absolute}
a{color:inherit;text-decoration:none}
.btn{position:absolute;background:var(--orange);color:var(--white);font:700 12px "Roboto",Arial,sans-serif;letter-spacing:.5px;text-transform:uppercase;display:flex;align-items:center;justify-content:center}

/* header */
.site-header{top:0;left:0;width:1200px;height:98px;background:var(--white)}
.brand{left:134px;top:22px;display:flex;align-items:center;gap:12px;font:400 22px "Open Sans",Arial,sans-serif;color:var(--ink)}
.brand-dot{width:14px;height:14px;border-radius:50%;background:var(--ink)}
.utility{right:134px;top:22px;display:flex;align-items:center;gap:22px;font:500 11px "Roboto",Arial,sans-serif;color:var(--ink)}
.utility .phone{text-decoration:underline}
.utility .cart{border:1px solid var(--ink);padding:5px 9px}
.utility svg{vertical-align:-2px;margin-right:5px}
.main-nav{right:134px;top:64px;display:flex;gap:22px;font:600 11px "Open Sans",Arial,sans-serif;color:var(--ink);text-transform:uppercase}
.main-nav a{padding:5px 8px}
.main-nav .active{background:var(--ink);color:var(--white)}

/* hero */
.hero{top:98px;left:0;width:1200px;height:490px;background:radial-gradient(circle at 30% 40%,#3cb0e4,#1a9ad6 60%,#168ac4)}
.hero-kicker{top:172px;left:0;width:1200px;text-align:center;font:700 22px "Open Sans",Arial,sans-serif;color:var(--white);letter-spacing:1px;display:flex;justify-content:center;align-items:center;gap:16px}
.hero-kicker::before,.hero-kicker::after{content:"";width:80px;height:2px;background:var(--white)}
.hero-title{top:205px;left:0;width:1200px;text-align:center;font:700 44px "Open Sans",Arial,sans-serif;color:var(--white);text-transform:uppercase}
.hero-cta{top:288px;left:532px;width:136px;height:40px;background:#4a4a4a;color:var(--white);font:600 16px "Open Sans",Arial,sans-serif;display:flex;align-items:center;justify-content:center;text-transform:uppercase}
.hero-dots{top:428px;left:0;width:1200px;display:flex;justify-content:center;gap:12px}
.hero-dots span{width:10px;height:10px;border-radius:50%;background:rgba(255,255,255,.6)}
.hero-dots span.on{background:var(--white)}

/* featured product */
.product-main{left:134px;top:637px;width:514px;height:331px;background:linear-gradient(160deg,#5a4a3e,#8a5238 45%,#b5a896 75%,#6b7a55)}
.thumb{top:979px;width:160px;height:103px}
.thumb-1{left:134px;background:linear-gradient(135deg,#a86868,#6b3e45)}
.thumb-2{left:308px;background:linear-gradient(135deg,#7a5a8e,#b6a0b8)}
.thumb-3{left:485px;background:linear-gradient(135deg,#4a3a35,#7e6e62)}
.product-title{left:731px;top:638px;font:400 24px "Open Sans",Arial,sans-serif;color:var(--ink)}
.product-price{left:731px;top:669px;font:700 28px "Open Sans",Arial,sans-serif;color:var(--ink)}
.qty-label{left:734px;top:727px;font:500 9px "Roboto",Arial,sans-serif;color:var(--ink)}
.qty{left:734px;top:748px;width:74px;height:36px;border:1px solid #bbb;font:400 12px "Roboto",Arial,sans-serif;color:var(--ink);display:flex;align-items:center;justify-content:space-between;padding:0 12px}
.product-copy{left:731px;width:335px;font:400 12px/19px "Roboto",Arial,sans-serif;color:var(--text);text-align:justify}

/* about */
.about{top:1140px;left:0;width:1200px;height:413px;background:var(--band)}
.about-kicker{left:141px;top:1198px;font:400 26px "Open Sans",Arial,sans-serif;color:var(--ink)}
.about-title{left:141px;top:1232px;font:700 26px "Open Sans",Arial,sans-serif;color:var(--orange);text-transform:uppercase}
.about-copy{left:141px;top:1285px;width:360px;font:400 12.5px/19px "Roboto",Arial,sans-serif;color:var(--text);text-align:justify}
.about-image{left:586px;top:1187px;width:482px;height:315px;background:linear-gradient(150deg,#f4e9e2,#e9b9a6 40%,#f6efe9 60%,#d9a08e)}

/* events */
.section-title{font:400 26px "Open Sans",Arial,sans-serif;color:var(--ink)}
.event-card,.product-card{width:295px}
.event-card{top:1663px;height:346px;background:var(--card)}
.event-image{position:absolute;left:13px;top:13px;width:269px;height:170px}
.card-title{position:absolute;left:26px;font:500 14px/19px "Roboto",Arial,sans-serif;color:var(--ink);width:245px}
.card-copy{position:absolute;left:26px;font:400 11px/16px "Roboto",Arial,sans-serif;color:var(--muted);width:245px}
.card-link{position:absolute;left:26px;font:700 10px "Roboto",Arial,sans-serif;color:var(--orange);text-transform:uppercase}

/* feature band */
.feature-image{left:0;top:2079px;width:597px;height:451px;background:linear-gradient(160deg,#6a4a3a,#9ec6c8 35%,#7aa46a 60%,#c8e0e0)}
.feature-panel{left:597px;top:2079px;width:603px;height:451px;background:var(--band)}
.feature-title{left:670px;top:2126px;width:300px;font:400 20px/32px "Open Sans",Arial,sans-serif;color:var(--ink)}
.feature-list{left:686px;top:2214px;list-style:none;font:400 12px "Roboto",Arial,sans-serif;color:var(--text)}
.feature-list li{height:29px;display:flex;align-items:center;gap:16px}
.feature-list li::before{content:"";border-left:5px solid var(--ink);border-top:4px solid transparent;border-bottom:4px solid transparent}

/* products */
.product-card{top:2635px;height:335px;border:1px solid var(--line);background:var(--white)}
.product-image{position:absolute;left:13px;top:13px;width:267px;height:174px}
.product-price-sm{position:absolute;left:22px;top:241px;font:400 20px "Open Sans",Arial,sans-serif;color:var(--ink)}

/* footer */
.site-footer{top:3033px;left:0;width:1200px;height:244px;background:var(--band)}
.footer-brand{left:141px;top:3112px;display:flex;align-items:center;gap:12px;font:400 20px "Open Sans",Arial,sans-serif;color:var(--ink)}
.footer-col h4{font:700 10px "Roboto",Arial,sans-serif;color:var(--ink);text-transform:uppercase;margin-bottom:16px}
.footer-col p{font:400 11px/18px "Roboto",Arial,sans-serif;color:var(--text)}
.newsletter-input{left:876px;top:3118px;width:192px;height:33px;background:var(--white);border:1px solid var(--line);font:400 11px "Roboto",Arial,sans-serif;color:var(--muted);display:flex;align-items:center;padding-left:14px}
.bottom-bar{top:3277px;left:0;width:1200px;height:75px;background:var(--white)}
.follow{left:132px;top:3309px;display:flex;align-items:center;gap:12px;font:700 10px "Roboto",Arial,sans-serif;color:var(--ink);text-transform:uppercase}
.follow span.icon{width:12px;height:12px;border-radius:50%;background:var(--ink)}
.copyright{right:132px;top:3310px;font:400 10px "Roboto",Arial,sans-serif;color:var(--muted)}
</style>
</head>
<body>

<header class="site-header abs">
  <div class="brand abs"><span class="brand-dot"></span>ta belle vitrine</div>
  <div class="utility abs">
    <span><svg width="11" height="11" viewBox="0 0 12 12"><path d="M2 1h3l1 3-2 1a7 7 0 0 0 3 3l1-2 3 1v3c-6 1-10-3-9-9z" fill="#1f1f1f"/></svg>CALL : <span class="phone">555.014.2290</span></span>
    <span><svg width="11" height="11" viewBox="0 0 12 12"><path d="M1 11l1-3 6-6 2 2-6 6z" fill="#1f1f1f"/></svg>REGISTER</span>
    <span><svg width="11" height="11" viewBox="0 0 12 12"><rect x="2" y="5" width="8" height="6" fill="#1f1f1f"/><path d="M4 5V3a2 2 0 0 1 4 0v2" stroke="#1f1f1f" fill="none"/></svg>LOGIN</span>
    <span class="cart"><svg width="11" height="11" viewBox="0 0 12 12"><path d="M0 1h2l2 7h6l2-5H3" stroke="#1f1f1f" fill="none"/><circle cx="5" cy="10.5" r="1" fill="#1f1f1f"/><circle cx="9" cy="10.5" r="1" fill="#1f1f1f"/></svg>MY CART (0)</span>
  </div>
  <nav class="main-nav abs">
    <a class="active" href="#">Home</a><a href="#">About us</a><a href="#">Products</a><a href="#">Blog</a><a href="#">Contact us</a>
  </nav>
</header>

<section class="hero abs" role="img" aria-label="Blue marbled floral pattern banner"></section>
<div class="hero-kicker abs">WELCOME TO</div>
<h1 class="hero-title abs">Ta Belle Vitrine</h1>
<a class="hero-cta abs" href="#">Shop now</a>
<div class="hero-dots abs"><span></span><span class="on"></span><span></span><span></span><span></span></div>

<div class="product-main abs" role="img" aria-label="Marbling tray with swirled paint on water"></div>
<div class="thumb thumb-1 abs" role="img" aria-label="Hands working a marbling pattern"></div>
<div class="thumb thumb-2 abs" role="img" aria-label="Purple marbled paper"></div>
<div class="thumb thumb-3 abs" role="img" aria-label="Paint jars beside a marbling tray"></div>
<h2 class="product-title abs">Marbal Art</h2>
<div class="product-price abs">$125.99</div>
<div class="qty-label abs">QTY</div>
<div class="qty abs">1<svg width="7" height="12" viewBox="0 0 7 12"><path d="M0 5l3.5-4L7 5zM0 7l3.5 4L7 7z" fill="#1f1f1f"/></svg></div>
<a class="btn" style="left:825px;top:748px;width:116px;height:36px" href="#">Buy now</a>
<p class="product-copy abs" style="top:826px">Lorem ipsum is a pseudo-Latin text used in web design, typography, layout, and printing in place of English to emphasise design elements over content. It's also called placeholder (or filler) text. It's a convenient tool for mock-ups. It helps to outline the visual elements of a document or presentation, eg typog</p>
<p class="product-copy abs" style="top:962px">In a professional context it often happens that private or corporate clients corder a publication to be made and presented with the actual content still not being ready. Think of a news blog that's filled</p>

<section class="about abs"></section>
<div class="about-kicker abs">About</div>
<h2 class="about-title abs">Ta Belle Vitrine</h2>
<p class="about-copy abs">Lorem ipsum is a pseudo-Latin text used in web design, typography, layout, and printing in place of English to emphasise design elements over content. It's also called placeholder (or filler) text. It's a convenient tool for mock-ups. It helps to outline the visual elements of a document or presentation, eg typog</p>
<a class="btn" style="left:141px;top:1406px;width:118px;height:36px" href="#">Read more</a>
<div class="about-image abs" role="img" aria-label="Soft pink and white marbled swirl"></div>

<h2 class="section-title abs" style="left:132px;top:1605px">Latest Events</h2>
<a class="btn" style="left:930px;top:1611px;width:136px;height:27px;font-size:11px" href="#">View all events</a>

<article class="event-card abs" style="left:132px">
  <div class="event-image" role="img" aria-label="Orange and turquoise symmetric marbled print" style="background:linear-gradient(135deg,#d8643e,#3ab2c0 50%,#d8643e)"></div>
  <h3 class="card-title" style="top:200px">Lorem ipsum is a pseudo-Latin text used in web design.</h3>
  <p class="card-copy" style="top:248px">Lorem ipsum is a pseudo-Latin text used in web design, typography, layout, and printing</p>
  <a class="card-link" style="top:302px" href="#">Read more</a>
</article>
<article class="event-card abs" style="left:454px">
  <div class="event-image" role="img" aria-label="Pink and navy stone-pattern marbled paper" style="background:linear-gradient(135deg,#c8448a,#2e3c78 50%,#d76aa8)"></div>
  <h3 class="card-title" style="top:200px">Lorem ipsum is a pseudo-Latin text used in web design.</h3>
  <p class="card-copy" style="top:248px">Lorem ipsum is a pseudo-Latin text used in web design, typography, layout, and printing</p>
  <a class="card-link" style="top:302px" href="#">Read more</a>
</article>
<article class="event-card abs" style="left:776px">
  <div class="event-image" role="img" aria-label="Green and grey cell marbling pattern" style="background:linear-gradient(135deg,#8a9a7a,#3e3a3a 50%,#a8b89a)"></div>
  <h3 class="card-title" style="top:200px">Lorem ipsum is a pseudo-Latin text used in web design.</h3>
  <p class="card-copy" style="top:248px">Lorem ipsum is a pseudo-Latin text used in web design, typography, layout, and printing</p>
  <a class="card-link" style="top:302px" href="#">Read more</a>
</article>

<div class="feature-image abs" role="img" aria-label="Marbling tray with floral pattern and paint jars"></div>
<section class="feature-panel abs"></section>
<h2 class="feature-title abs">Lorem Ipsum is simply dummy text of the printing</h2>
<ul class="feature-list abs">
  <li>Lorem ipsum is a pseudo-Latin</li>
  <li>There are many variations of passage</li>
  <li>It is a long established fac</li>
  <li>The standard chunk of Lorem</li>
  <li>Lorem Ipsum generators on</li>
  <li>Various versions have</li>
</ul>
<a class="btn" style="left:686px;top:2425px;width:116px;height:34px" href="#">Read more</a>

<h2 class="section-title abs" style="left:132px;top:2577px">Products</h2>
<svg class="abs" style="left:1028px;top:2586px" width="46" height="16" viewBox="0 0 46 16"><path d="M8 2l-6 6 6 6" stroke="#1f1f1f" stroke-width="2.5" fill="none"/><path d="M38 2l6 6-6 6" stroke="#1f1f1f" stroke-width="2.5" fill="none"/></svg>

<article class="product-card abs" style="left:132px">
  <div class="product-image" role="img" aria-label="Lilac marbled print with pink flecks" style="background:linear-gradient(135deg,#cfc6e6,#e8cfe0 50%,#b9b4da)"></div>
  <h3 class="card-title" style="top:206px;left:22px">Lorem ipsum is a pseudo-Latin text</h3>
  <div class="product-price-sm">$29.99</div>
  <a class="btn" style="left:22px;top:276px;width:96px;height:32px" href="#">Buy now</a>
</article>
<article class="product-card abs" style="left:454px">
  <div class="product-image" role="img" aria-label="Peach marble with gold veins" style="background:linear-gradient(135deg,#f3c2b4,#e8b27a 50%,#f5cfc0)"></div>
  <h3 class="card-title" style="top:206px;left:22px">Lorem ipsum is a pseudo-Latin text</h3>
  <div class="product-price-sm">$29.99</div>
  <a class="btn" style="left:22px;top:276px;width:96px;height:32px" href="#">Buy now</a>
</article>
<article class="product-card abs" style="left:776px">
  <div class="product-image" role="img" aria-label="Deep teal marble with gold veins" style="background:linear-gradient(135deg,#0f3a5a,#1f6a80 50%,#c8a84a)"></div>
  <h3 class="card-title" style="top:206px;left:22px">Lorem ipsum is a pseudo-Latin text</h3>
  <div class="product-price-sm">$29.99</div>
  <a class="btn" style="left:22px;top:276px;width:96px;height:32px" href="#">Buy now</a>
</article>

<footer class="site-footer abs"></footer>
<div class="footer-brand abs"><span class="brand-dot"></span>ta belle vitrine</div>
<div class="footer-col abs" style="left:349px;top:3083px">
  <h4>Contact us</h4>
  <p>27 Larkfield Row<br>Mareton, TX 70418</p>
  <p style="margin-top:14px">555.014.2290</p>
  <p style="margin-top:14px">info@tavorinque.com</p>
</div>
<div class="footer-col abs" style="left:536px;top:3083px">
  <h4>Menu</h4>
  <p>Home<br>About us<br>Services<br>Products<br>Blog<br>Contact us</p>
</div>
<div class="footer-col abs" style="left:691px;top:3083px">
  <h4>My account</h4>
  <p>My Account<br>Login<br>Register<br>My Wishlist<br>My Cart</p>
</div>
<div class="footer-col abs" style="left:876px;top:3083px">
  <h4>Newsletter signup</h4>
</div>
<div class="newsletter-input abs">E mail id</div>
<a class="btn" style="left:876px;top:3165px;width:76px;height:30px" href="#">Signup</a>

<div class="bottom-bar abs"></div>
<div class="follow abs">Follow us <span class="icon"></span><span class="icon"></span><span class="icon"></span><span class="icon"></span></div>
<div class="copyright abs">Copyrights @ 2017 All Rights Reserved</div>

</body>
</html>
```